Managed IT services business card design

We haven't needed a business card since the founding of the business in 2005. All our clients have been coming through word of mouth. And lately more and more existing clients are requesting for our business cards to pass on to their contacts in recommending us.
So we needing a business card design. We use various innovative solutions and methodologies to provide IT services to small businesses in managing their IT systems. Our role is the same as an in-house, full-time IT Manager for our clients, but outsourced. So we take care of all our clients' IT needs, just as an IT Manager would be expected to perform.
We have a holding website, which we're happy to leave for now. If we can use the same logo would be great - www.lumadesk.com.au
Preferred colours are shades of are white, grey and black.
We pride our business with the following traits: proactive, good service, prompt response, trustworthy.
Target Market(s)
Small businesses of any industry
Industry/Entity Type
Business

```html
<!DOCTYPE html>
<html lang="en">
<head>
<meta charset="utf-8">
<title>lumadesk business card</title>
<link rel="stylesheet" href="https://fonts.googleapis.com/css2?family=Open+Sans:wght@400;600;700&display=swap">
<style>
  :root {
    --page: #e6e6e6;
    --card-white: #ffffff;
    --card-shade: #e9e9e9;
    --band-dark: #111111;
    --band-mid: #3c3c3c;
    --rim: #bdbdbd;
    --ink: #1a1a1a;
    --ink-soft: #333333;
    --on-dark: #f2f2f2;
  }
  * { box-sizing: border-box; margin: 0; padding: 0; }
  html, body { width: 1200px; height: 1000px; overflow: hidden; }
  body {
    background: var(--page);
    font-family: "Open Sans", sans-serif;
    position: relative;
  }
  .card {
    position: absolute;
    left: 100px; top: 225px;
    width: 1000px; height: 550px;
    overflow: hidden;
    box-shadow: 0 10px 30px rgba(0,0,0,0.25);
    background: var(--card-white);
  }
  .card-art { position: absolute; inset: 0; }
  .brand {
    position: absolute; left: 0; right: 0; top: 88px;
    text-align: center;
    font-size: 72px; font-weight: 400;
    letter-spacing: 18px;
    color: var(--ink);
  }
  .holder { position: absolute; left: 0; right: 0; top: 228px; text-align: center; }
  .holder-name { font-size: 38px; font-weight: 700; color: var(--ink-soft); }
  .holder-role { font-size: 26px; font-weight: 400; color: var(--ink-soft); margin-top: 2px; }
  .contact {
    position: absolute;
    font-size: 22px; color: var(--on-dark);
    display: flex; flex-direction: column; gap: 14px;
  }
  .contact-left { left: 40px; top: 448px; }
  .contact-right { right: 40px; top: 434px; }
  .contact-line { display: flex; align-items: center; gap: 14px; height: 28px; }
  .contact-line svg { width: 26px; height: 26px; flex: none; }
</style>
</head>
<body>
  <section class="card" aria-label="Business card">
    <svg class="card-art" viewBox="0 0 1000 550" preserveAspectRatio="none" aria-hidden="true">
      <defs>
        <radialGradient id="paper" cx="0.5" cy="0.35" r="0.7">
          <stop offset="0.6" stop-color="var(--card-white)"/>
          <stop offset="1" stop-color="var(--card-shade)"/>
        </radialGradient>
        <linearGradient id="band" x1="0" y1="0" x2="0" y2="1">
          <stop offset="0" stop-color="var(--band-dark)"/>
          <stop offset="1" stop-color="var(--band-mid)"/>
        </linearGradient>
      </defs>
      <rect width="1000" height="550" fill="url(#paper)"/>
      <path d="M0 400 Q 380 430 1000 300 V550 H0 Z" fill="url(#band)"/>
      <path d="M0 392 Q 380 422 1000 292" fill="none" stroke="var(--rim)" stroke-width="6"/>
      <path d="M0 408 Q 380 440 1000 312" fill="none" stroke="#555" stroke-width="2" opacity="0.6"/>
    </svg>

    <div class="brand">lumadesk</div>

    <div class="holder">
      <div class="holder-name">Name Title</div>
      <div class="holder-role">designation</div>
    </div>

    <div class="contact contact-left">
      <div class="contact-line"><span>Harwood Lane, Melbourne</span></div>
      <div class="contact-line">
        <svg viewBox="0 0 26 26" aria-hidden="true"><rect width="26" height="26" rx="4" fill="#fff"/><path d="M8 6c-1 1-2 3 0 7s5 7 8 7c1 0 2-1 3-2l-3-3-2 1c-1-1-3-3-4-5l1-2z" fill="#111"/></svg>
        <span>+61 412 555 018</span>
      </div>
    </div>

    <div class="contact contact-right">
      <div class="contact-line">
        <svg viewBox="0 0 26 26" aria-hidden="true"><circle cx="13" cy="13" r="13" fill="#fff"/><rect x="6" y="8" width="14" height="10" fill="#111"/><path d="M6 8l7 6 7-6" fill="none" stroke="#fff" stroke-width="1.5"/></svg>
        <span>mail@lumadesk.com.au</span>
      </div>
      <div class="contact-line">
        <svg viewBox="0 0 26 26" aria-hidden="true"><circle cx="13" cy="13" r="11" fill="none" stroke="#fff" stroke-width="2"/><ellipse cx="13" cy="13" rx="5" ry="11" fill="none" stroke="#fff" stroke-width="1.5"/><path d="M2 13h22M4 7h18M4 19h18" stroke="#fff" stroke-width="1.5"/></svg>
        <span>www.lumadesk.com.au</span>
      </div>
    </div>
  </section>
</body>
</html>
```